Business card

We need a business card design for our company based in Auckland , New Zealand called 'Ridge + Studio Ltd'. We provide architectural services. We would like to see designs that use the max. three colours (such as white, black, grey) The final design should communicate financial safety and growth."
Also I will provide our company logo. I would like to the logo to be embeded onto our business card.

Target Market(s)

new residential house, alteration & addition & light commericila design & drafting service

Industry/Entity Type

Architecture

Contact Information for Business Card

Company name: ridge + studio Ltd.
Name: Mark Delford
Job title: architectural designer & Design LBP
email address: mark@rplusd.co.nz
mobile number: 02 5163 2290
web site: www.rplusd.co.nz

Requirements
Must have
• My project must have..
• - embeded logo (attached company logo)
• I don't have a bigger version for our company logo, but I have one old one, so you can remove the word from it)
• - insert the attached small BKTW logo & LBP logo
• - creative, simple and clear business card.
• - Max. three colours
Nice to have
• - Here are the samples I would like to share with you: http://www.plimvora.com/blog/minimalistic-business-card-designs/
• I would like to have my business card like one of the creation.
Should not have
• TBA

```html
<!DOCTYPE html>
<html lang="en">
<head>
<meta charset="utf-8">
<title>Ridge + Studio Ltd — Business Card</title>
<link rel="stylesheet" href="https://fonts.googleapis.com/css2?family=Tinos:wght@400;700&display=swap">
<style>
  :root {
    --ink: #111111;
    --paper: #ffffff;
    --grey: #8a8a8a;
    --badge: #333333;
    --badge-ring: #999999;
    --divider: #bbbbbb;
    --muted-ink: #555555;
    --backdrop: #d9d9d9;
  }
  * { margin: 0; padding: 0; box-sizing: border-box; }
  html, body {
    width: 1200px;
    height: 950px;
    overflow: hidden;
    background: var(--backdrop);
    font-family: "Tinos", "Times New Roman", serif;
  }
  .canvas {
    position: relative;
    width: 1200px;
    height: 950px;
  }
  .card {
    position: absolute;
    left: 250px;
    width: 700px;
    height: 427px;
    background: var(--paper);
    overflow: hidden;
    box-shadow: 0 2px 6px rgba(0,0,0,0.15);
  }
  .card--front { top: 40px; }
  .card--back { top: 490px; }

  /* Front */
  .brand {
    position: absolute;
    left: 50%;
    top: 50%;
    transform: translate(-50%, -50%);
    display: flex;
    align-items: center;
    gap: 18px;
  }
  .brand__dot {
    width: 64px;
    height: 64px;
    border-radius: 50%;
    background: var(--ink);
  }
  .brand__name {
    font-size: 34px;
    font-weight: 400;
    color: var(--ink);
    letter-spacing: 1px;
    white-space: nowrap;
  }
  .front-web {
    position: absolute;
    right: 36px;
    bottom: 48px;
    font-size: 15px;
    line-height: 1;
    color: var(--grey);
    letter-spacing: 0.5px;
    writing-mode: vertical-rl;
    transform: rotate(180deg);
    white-space: nowrap;
  }

  /* Back */
  .back-band {
    position: absolute;
    left: 0; top: 176px;
    width: 100%;
    height: 251px;
    background: var(--ink);
  }
  .back-rule {
    position: absolute;
    left: 0; top: 170px;
    width: 100%;
    height: 2px;
    background: var(--grey);
  }
  .affiliations {
    position: absolute;
    left: 48px;
    top: 40px;
    display: flex;
    align-items: center;
    gap: 24px;
  }
  .affiliation__name {
    font-size: 44px;
    font-weight: 700;
    color: var(--muted-ink);
    letter-spacing: -1px;
  }
  .affiliation__divider {
    width: 1px;
    height: 80px;
    background: var(--divider);
  }
  .affiliation__badge {
    width: 96px;
    height: 96px;
    border-radius: 50%;
    background: var(--badge);
    border: 4px solid var(--badge-ring);
  }
  .contact {
    position: absolute;
    left: 48px;
    top: 208px;
    color: var(--paper);
  }
  .contact__name {
    font-size: 28px;
    font-weight: 400;
    line-height: 1.2;
  }
  .contact__role {
    font-size: 24px;
    line-height: 1.3;
    margin-bottom: 14px;
    white-space: nowrap;
  }
  .contact__line {
    font-size: 16px;
    line-height: 1.7;
    white-space: nowrap;
  }
  .back-brand {
    position: absolute;
    right: 44px;
    top: 214px;
    display: flex;
    align-items: center;
    gap: 12px;
  }
  .back-brand__dot {
    width: 56px;
    height: 56px;
    border-radius: 50%;
    background: var(--paper);
  }
  .back-brand__name {
    font-size: 22px;
    color: var(--paper);
    white-space: nowrap;
  }
</style>
</head>
<body>
<main class="canvas">

  <section class="card card--front" aria-label="Card front">
    <div class="brand">
      <span class="brand__dot"></span>
      <span class="brand__name">ridge + studio</span>
    </div>
    <p class="front-web">www.rplusd.co.nz</p>
  </section>

  <section class="card card--back" aria-label="Card back">
    <div class="back-band"></div>
    <div class="back-rule"></div>

    <div class="affiliations">
      <span class="affiliation__name">BKTW</span>
      <span class="affiliation__divider"></span>
      <span class="affiliation__badge" role="img" aria-label="Licensed practitioner badge"></span>
    </div>

    <div class="contact">
      <p class="contact__name">Mark Delford</p>
      <p class="contact__role">architectural designer &amp; Design LBP</p>
      <p class="contact__line">Ridge + Studio Ltd. | M : 02 5163 2290</p>
      <p class="contact__line">E : mark@rplusd.co.nz &nbsp;W : www.rplusd.co.nz</p>
    </div>

    <div class="back-brand">
      <span class="back-brand__dot"></span>
      <span class="back-brand__name">ridge + studio</span>
    </div>
  </section>

</main>
</body>
</html>
```